Pebble Hop - mobile play centre poster designs

Who are we - we are a mobile playground business that specialises in providing entertainment to children in a safe, clean environment either at home or in a function centre. Brief - create 4 different signs to be displayed on our playgrounds. Please find attached 3 photos from our competitors to use as a guide. Corflute sign - size A1 Toddler zone - size A1 Playground rules - size A4 No climbing - size 20cmx8cm sending through photos and documents now.
Colors
Designer to choose colors to be used in the design.
Requirements
Must have
- Colour, be very specific with the rules, pictures

```html
<!DOCTYPE html>
<html lang="en">
<head>
<meta charset="utf-8">
<title>No Climbing – Pebble Hop</title>
<link href="https://fonts.googleapis.com/css2?family=Anton&display=swap" rel="stylesheet">
<style>
  :root{
    --backdrop:#e4e4e2;
    --frame-yellow:#f4d21c;
    --frame-yellow-light:#f8e25a;
    --bamboo-green:#8cc63f;
    --bamboo-dark:#5f9a2a;
    --panel-cream:#fbf7dc;
    --panel-sky:#dcefe6;
    --panel-leaf:#cfe3a4;
    --stop-red:#e3262b;
    --net-grey:#b9b9b9;
    --word-red:#e8242a;
    --word-orange:#f5821f;
  }
  *{margin:0;padding:0;box-sizing:border-box}
  html,body{width:1200px;height:603px;overflow:hidden;background:var(--backdrop)}
  .sign{
    position:absolute;left:117px;top:92px;width:950px;height:375px;
    background:linear-gradient(90deg,var(--frame-yellow) 0 50%,var(--frame-yellow-light) 50% 100%);
    background-size:60px 100%;
    box-shadow:0 6px 14px rgba(0,0,0,.18);
  }
  .bamboo-frame{
    position:absolute;left:22px;top:20px;right:22px;bottom:20px;
    border:10px solid var(--bamboo-green);
    outline:2px solid var(--bamboo-dark);
  }
  .jungle-backdrop{
    position:absolute;inset:0;
    background:
      radial-gradient(ellipse 60% 40% at 70% 20%,var(--panel-sky),transparent 70%),
      linear-gradient(180deg,var(--panel-cream) 0%,var(--panel-cream) 55%,var(--panel-leaf) 100%);
  }
  .stop-icon{position:absolute;left:75px;top:100px;width:220px;height:220px}
  .headline{
    position:absolute;left:366px;top:122px;
    font-family:"Anton",sans-serif;font-size:112px;line-height:1;letter-spacing:1px;
    white-space:nowrap;
  }
  .headline .no{color:var(--word-red);margin-right:14px}
  .headline .climbing{color:var(--word-orange)}
</style>
</head>
<body>
  <div class="sign">
    <div class="bamboo-frame">
      <div class="jungle-backdrop" role="img" aria-label="Soft jungle leaves and clouds background"></div>
    </div>
    <svg class="stop-icon" viewBox="0 0 220 220">
      <circle cx="110" cy="110" r="88" fill="var(--net-grey)" role="img" aria-label="Climber on a rope net pictogram"/>
      <circle cx="110" cy="110" r="95" fill="none" stroke="var(--stop-red)" stroke-width="18"/>
      <line x1="45" y1="45" x2="175" y2="175" stroke="var(--stop-red)" stroke-width="18"/>
    </svg>
    <div class="headline"><span class="no">NO</span><span class="climbing">CLIMBING</span></div>
  </div>
</body>
</html>
```